Building company buisness cards

We are looking for a sharp modern new look for our business cards.We are a New Zealand based company that specialises in house and land packages.We have attached a photo of the current logo and would like to see if it can be improved somehow if needed.We are open to any colours but we have chosen Black and White at this stage. Feel free to change the font and make the logo smarter looking.Play with the colours and see what looks best.We want a card that looks so good know one will want to throw it away!

Target Market(s)

Building profesonals, home buyers

Industry/Entity Type

Building

Contact Information for Business Card

Garrick Tenwood
0275390628
garrickt@hartvale.co.nz

Font styles to use
Serif
Sans Serif

Colors

Designer to choose colors to be used in the design.

Requirements
Must have
• Just the logo on one side and details on the other
• Clean simple looking card
Nice to have
• Round corners and detail like raised or spot UV
• Something that stands out
Should not have
• To title needed, Director etc

```html
<!DOCTYPE html>
<html lang="en">
<head>
<meta charset="utf-8">
<title>Hartvale – Business Cards</title>
<link href="https://fonts.googleapis.com/css2?family=Inter:wght@400;500&display=swap" rel="stylesheet">
<style>
  :root {
    --stage: #b9b9b9;
    --card-dark: #0c0c0c;
    --card-light: #ffffff;
    --ink: #111111;
    --ink-soft: #2a2a2a;
    --paper-text: #ffffff;
    --rule: #1a1a1a;
  }
  * { box-sizing: border-box; margin: 0; padding: 0; }
  html, body {
    width: 1200px; height: 930px; overflow: hidden;
    background: var(--stage);
  }
  .stage { position: relative; width: 1200px; height: 930px; }

  .card {
    position: absolute; width: 560px; height: 340px;
    border-radius: 26px; overflow: hidden;
    box-shadow: 0 10px 24px rgba(0,0,0,0.18);
    font-family: "Inter", Arial, sans-serif;
  }

  /* Shared company name, set in the card's text font */
  .company-name {
    font-family: "Inter", Arial, sans-serif;
    font-weight: 500; line-height: 1;
    letter-spacing: 0.06em; text-transform: uppercase;
  }

  /* Logo side */
  .card--back { left: 60px; top: 80px; background: var(--card-dark); }
  .card--back .pattern-area {
    position: absolute; inset: 0;
    background: linear-gradient(135deg, #161616, #0a0a0a);
  }
  .card--back .company-name {
    position: absolute; right: 46px; bottom: 42px;
    font-size: 22px; color: var(--paper-text);
  }

  /* Details side */
  .card--front { left: 580px; top: 500px; background: var(--card-light); color: var(--ink); }
  .card--front .company-name {
    position: absolute; right: 40px; top: 46px;
    font-size: 40px; color: var(--ink);
  }

  .divider-full {
    position: absolute; left: 40px; right: 40px; top: 124px;
    border-top: 1px solid var(--rule);
  }
  .address {
    position: absolute; right: 40px; top: 142px;
    text-align: right; font-size: 13px; line-height: 1.45; color: var(--ink-soft);
  }
  .person { position: absolute; left: 40px; top: 200px; }
  .person__name { font-size: 20px; font-weight: 500; letter-spacing: 0.04em; text-transform: uppercase; }
  .divider-short {
    position: absolute; left: 40px; top: 238px; width: 210px;
    border-top: 1px solid var(--rule);
  }
  .contacts {
    position: absolute; left: 40px; top: 252px; list-style: none;
    font-size: 13px; color: var(--ink-soft);
  }
  .contacts li { display: flex; align-items: center; gap: 8px; height: 20px; }
  .contacts svg { width: 10px; height: 10px; fill: var(--ink); flex: none; }
</style>
</head>
<body>
<main class="stage">

  <section class="card card--back" aria-label="Card logo side">
    <div class="pattern-area" role="img" aria-label="Faint repeated company name pattern in dark grey on black"></div>
    <p class="company-name">Hartvale</p>
  </section>

  <section class="card card--front" aria-label="Card details side">
    <p class="company-name">Hartvale</p>
    <div class="divider-full"></div>
    <p class="address">214b Carrow Street,<br>Ashford, NZ, 8042</p>
    <div class="person">
      <p class="person__name">Garrick Tenwood</p>
    </div>
    <div class="divider-short"></div>
    <ul class="contacts">
      <li>
        <svg viewBox="0 0 10 10" aria-hidden="true"><path d="M2 0.5 L3.6 0.5 L4.2 2.8 L3.1 3.7 Q4 5.9 6.3 6.9 L7.2 5.8 L9.5 6.4 L9.5 8 Q9.5 9.5 8 9.5 Q0.5 9 0.5 2 Q0.5 0.5 2 0.5 Z"/></svg>
        0275390628
      </li>
      <li>
        <svg viewBox="0 0 10 10" aria-hidden="true"><path d="M0.5 2 H9.5 V8.5 H0.5 Z M1.2 2.6 L5 5.4 L8.8 2.6 V7.9 H1.2 Z" fill-rule="evenodd"/></svg>
        garrickt@hartvale.co.nz
      </li>
      <li>
        <svg viewBox="0 0 10 10" aria-hidden="true"><path d="M5 0.5 A4.5 4.5 0 1 0 5 9.5 A4.5 4.5 0 1 0 5 0.5 Z M5 1.5 A3.5 3.5 0 1 1 5 8.5 A3.5 3.5 0 1 1 5 1.5 Z M1.5 4.6 H8.5 V5.4 H1.5 Z M4.6 1.5 H5.4 V8.5 H4.6 Z" fill-rule="evenodd"/></svg>
        www.hartvale.co.nz
      </li>
    </ul>
  </section>

</main>
</body>
</html>
```